Elevating our current Business Card Design

We want to elevate our current business card with a new design to look like a zenith 300 company. We are a premium lubricant distributor (oil and grease).
We need 2 versions, version 1 is as per the uploaded a copy of our current business card with the English version.
For our Chinese version we need to use the front to be English in English and have the back of the card designed exactly like the front for all info to be in Chinese.
The design template needs to be such that we can amend the template with adding different information for each person's card.
The background colour of the card can be changed- we just need to clearly see all information on the card and logos.
The QJR and Ember steady logos cannot have any colour or display changes- only use the logos attached.
All logos need to be included and all information from the attached current card

```html
<!DOCTYPE html>
<html lang="en">
<head>
<meta charset="UTF-8">
<title>Meridian Lubricant Supply – Business Card</title>
<link href="https://fonts.googleapis.com/css2?family=Open+Sans:ital,wght@0,400;0,600;0,700;1,700&display=swap" rel="stylesheet">
<style>
  :root {
    --red: #e3262b;
    --red-deep: #b01a20;
    --gold: #e3a823;
    --ink: #1d1d1f;
    --card-dark: #222124;
    --paper: #ffffff;
    --stage: #3a3d42;
    --silver: #a8a9ad;
    --badge-orange: #f08a1c;
  }
  * { box-sizing: border-box; margin: 0; padding: 0; }
  html, body { width: 1200px; height: 780px; overflow: hidden; }
  body {
    background: var(--stage);
    font-family: "Open Sans", Arial, sans-serif;
    color: var(--ink);
  }
  .canvas {
    position: relative;
    width: 1200px; height: 780px;
    display: flex; align-items: center; justify-content: center; gap: 40px;
  }
  .card {
    position: relative;
    width: 540px; height: 310px;
    border-radius: 4px;
    overflow: hidden;
    box-shadow: 0 10px 30px rgba(0,0,0,.35);
  }

  /* ---------- Front ---------- */
  .card-front { background: var(--paper); }
  .brand-mark {
    position: absolute;
    display: flex; align-items: center; gap: 10px;
    font-weight: 700; color: var(--red); letter-spacing: 1px;
  }
  .brand-mark .dot { border-radius: 50%; background: var(--gold); flex: none; }
  .card-front .brand-mark { left: 292px; top: 40px; font-size: 34px; }
  .card-front .brand-mark .dot { width: 26px; height: 26px; }

  .person { position: absolute; left: 38px; top: 100px; }
  .person-name {
    font-size: 27px; font-weight: 700; font-style: italic; color: var(--red);
    line-height: 1.1;
  }
  .person-role { font-size: 14px; font-weight: 400; margin-top: 2px; }

  .divider {
    position: absolute; left: 262px; top: 150px;
    width: 1px; height: 95px; background: var(--ink);
  }

  .contacts { position: absolute; left: 276px; top: 146px; list-style: none; }
  .contacts li {
    display: flex; align-items: center; gap: 9px;
    font-size: 13px; line-height: 19px;
  }
  .contacts svg { width: 12px; height: 12px; flex: none; }

  .front-band {
    position: absolute; left: 0; bottom: 0; width: 100%; height: 34px;
    display: flex; align-items: stretch;
  }
  .band-address {
    flex: 1;
    background: linear-gradient(90deg, var(--red-deep), var(--red));
    color: var(--paper); font-size: 13px;
    display: flex; align-items: center; padding-left: 26px;
  }
  .band-company {
    width: 118px; background: var(--paper);
    border: 2px solid var(--red);
    display: flex; align-items: center; justify-content: center;
    font-size: 8px; font-weight: 700; color: var(--red); line-height: 1.1;
    text-align: center;
  }
  .band-partner {
    width: 88px; background: var(--red);
    display: flex; align-items: center; justify-content: center;
    color: var(--paper); font-size: 13px; font-weight: 700; letter-spacing: .5px;
  }
  .band-corner { width: 38px; background: var(--gold); }

  /* ---------- Back ---------- */
  .card-back { background: var(--card-dark); }
  .card-back .brand-mark { left: 150px; top: 90px; font-size: 50px; }
  .card-back .brand-mark .dot { width: 36px; height: 36px; }

  .back-strip {
    position: absolute; left: 22px; bottom: 22px;
    display: flex; align-items: center; gap: 12px;
  }
  .badge-ember {
    width: 40px; height: 26px; border-radius: 13px 13px 4px 4px;
    background: #d9d9dc;
  }
  .badge-cert {
    width: 28px; height: 28px; border-radius: 50%;
    background: var(--badge-orange);
    border: 4px solid var(--silver);
  }
  .back-company {
    height: 30px; padding: 0 10px;
    border: 2px solid var(--red);
    display: flex; align-items: center;
    font-size: 8px; font-weight: 700; color: var(--red); line-height: 1.1;
  }
  .back-partner {
    height: 30px; padding: 0 16px; background: var(--red);
    display: flex; align-items: center;
    color: var(--paper); font-size: 14px; font-weight: 700; letter-spacing: .5px;
  }
</style>
</head>
<body>
<main class="canvas">

  <!-- Front of card -->
  <section class="card card-front" aria-label="Business card front">
    <div class="brand-mark"><span class="dot"></span>MERIDIAN</div>

    <div class="person">
      <p class="person-name">Clara Vennet</p>
      <p class="person-role">Administration Executive</p>
    </div>

    <div class="divider"></div>

    <ul class="contacts">
      <li>
        <svg viewBox="0 0 12 12"><path d="M3 1l2 2.5-1.2 1.3a6 6 0 0 0 3.4 3.4L8.5 7 11 9l-1 2C5 11 1 7 1 2z" fill="var(--red)"/></svg>
        1300 000 411
      </li>
      <li>
        <svg viewBox="0 0 12 12"><rect x="3" y="1" width="6" height="10" rx="1" fill="none" stroke="var(--red)" stroke-width="1.2"/></svg>
        +61 400 555 019
      </li>
      <li>
        <svg viewBox="0 0 12 12"><rect x="1" y="4" width="10" height="7" rx="1" fill="var(--red)"/><rect x="3" y="1" width="6" height="4" fill="none" stroke="var(--red)"/></svg>
        +61 8 5550 1234
      </li>
      <li>
        <svg viewBox="0 0 12 12"><circle cx="6" cy="6" r="5" fill="var(--red)"/><path d="M1 6h10M6 1c-2 3-2 7 0 10M6 1c2 3 2 7 0 10" stroke="#fff" stroke-width=".8" fill="none"/></svg>
        www.meridianlube.com
      </li>
      <li>
        <svg viewBox="0 0 12 12"><rect x="1" y="3" width="10" height="7" fill="var(--red)"/><path d="M1 3l5 4 5-4" stroke="#fff" stroke-width=".9" fill="none"/></svg>
        clara.vennet@meridianlube.com
      </li>
    </ul>

    <div class="front-band">
      <div class="band-address">48 Freight Lane Harlow, WA 6190</div>
      <div class="band-company">MERIDIAN<br>LUBRICANT SUPPLY</div>
      <div class="band-partner">KESTREL</div>
      <div class="band-corner"></div>
    </div>
  </section>

  <!-- Back of card -->
  <section class="card card-back" aria-label="Business card back">
    <div class="brand-mark"><span class="dot"></span>MERIDIAN</div>

    <div class="back-strip">
      <div class="badge-ember" role="img" aria-label="Ember steady network member badge"></div>
      <div class="badge-cert" role="img" aria-label="QJR certification badge"></div>
      <div class="back-company">MERIDIAN<br>LUBRICANT SUPPLY</div>
      <div class="back-partner">KESTREL</div>
      <div class="badge-cert" role="img" aria-label="QJR certification badge"></div>
      <div class="badge-cert" role="img" aria-label="QJR certification badge"></div>
    </div>
  </section>

</main>
</body>
</html>
```